High-end Oceanfront Real Estate Group Needs Clean, Modern Web Design

I’m looking for a clean, professional, modern and beautiful homepage web design for a Real Estate group in Southern California, USA.

The group/company is “Marwick on the Shore,” and they specialize in high end (i.e. expensive), oceanfront real estate in the Orange County area.

The look and feel of the page should accentuate the brand qualities: luxurious/expensive, professional, and beautiful (Orange County is one of the most beautiful areas in all the US and we would love the site to emphasize the beautiful beaches and scenery it has to offer).

Looks we like:
• www.brantleyhomesrealty.example
• www.closedbyvane.example -- I think the design is pretty out-dated in this site, but I like the organization/layout of the site

Header Tags (I don’t know if we can fit all of these, may need a side-menu, but I’d prefer header title only if possible):
• Welcome
• Featured Listings
• Previously Sold
• Sell
• Property Search
• Team
• Videos
• Blog
• Explore O.C.
• Contact

I have attached the beach and logo pics that we would like to use as the header, a few pictures of the team, and one sample home/view pic which can be used in any of the other sections (for pictures of the homes, just find expensive oceanfront houses and that will be fine).

I promise to provide feedback to each and every design submission. I appreciate the hard work that all of you are putting into your designs. There can be only one contest winner, but I hope to give all of you helpful feedback to submit the best designs possible!

Target Market(s)

Very wealthy home owners of oceanfront properties. These properties are worth several millions of dollars, and thus the site and brand needs to be targeted to very wealthy, successful individuals and families (both US and international buyers).

Industry/Entity Type

Real Estate

Number of Pages Required

2 page

Requirements
Must have
• I don’t want to give too many requirements, because I want to let you all be creative. However, here are the few Must Haves:
• Must submit 2 page designs (a home page and a sub page)
• Must use logo provided
• Focus is mostly on homes, but I would like to include some beach/ocean imagery as well
• The first “item” on the home page should be an accordion/slider which shows pictures of homes and with 1 line of text: “List with the Leader” and two link buttons: “Sell Your Home” and “Buy Your Home”
• Color palette needs to be mainly blues--to match ocean and sky blue
• Exported in all major formats (psd,ai,eps,png,jpeg,etc)
Nice to have
• We don’t necessarily need all of these, but would like to feature most:
• List of videos
• “Meet the Team”—brief team bios and pics
• Link(s) to Blog
• “List with the Leader” – section on why they should choose this firm
• Featured Listings
• Previously Sold

```html
<!DOCTYPE html>
<html lang="en">
<head>
<meta charset="utf-8">
<title>Properties — Marwick on the Shore</title>
<link href="https://fonts.googleapis.com/css2?family=Arvo:wght@400;700&family=Raleway:wght@300;400;500;600&display=swap" rel="stylesheet">
<style>
:root{
  --brand:#1a6fb5;
  --brand-dark:#175f9c;
  --accent:#17a3e6;
  --accent-soft:#35b3ee;
  --ink:#222;
  --muted:#666;
  --line:#d6d6d6;
  --panel:#333333;
  --panel-line:#4a4a4a;
  --bar:#2f2f2f;
  --footer:#3b3b3d;
  --footer-deep:#2c2c2e;
  --orange:#f07a22;
  --white:#fff;
}
*{box-sizing:border-box;margin:0;padding:0}
html,body{width:698px;height:1200px;overflow:hidden}
body{position:relative;background:var(--white);font-family:'Raleway',sans-serif;color:var(--ink);font-size:9px}
.abs{position:absolute}

/* header */
.topbar{left:0;top:0;width:698px;height:30px;background:var(--bar)}
.hero-band{left:0;top:30px;width:698px;height:48px;background:linear-gradient(180deg,#cfe2f1 0%,#e9f1f7 55%,#f4f1ea 100%)}
.hero-band .ridge{position:absolute;right:0;bottom:0;width:200px;height:14px;background:linear-gradient(90deg,rgba(200,170,140,0),#c9a889 60%,#b79a7d)}
.brand{left:101px;top:0;width:114px;height:78px;background:var(--brand);display:flex;align-items:center;justify-content:center;text-align:center}
.brand span{color:var(--white);font-family:'Raleway',sans-serif;font-weight:300;font-size:15px;line-height:18px;letter-spacing:.5px}
.nav{left:229px;top:0;height:30px;display:flex;align-items:center;gap:0}
.nav a{color:var(--white);text-decoration:none;font-size:8.5px;font-weight:500;text-transform:uppercase;margin-right:13px;display:flex;align-items:center;gap:2px}
.nav a.current{color:var(--accent)}
.page-title{left:229px;top:45px;font-size:13px;font-weight:500;color:#222}

/* tabs & filters */
.tabs{left:100px;top:95px;width:368px;height:25px;border-bottom:1px solid var(--line);display:flex}
.tab{height:24px;padding:0 8px;display:flex;align-items:center;font-family:'Arvo',serif;font-size:11px;border:1px solid #bbb}
.tab.active{background:var(--brand);color:var(--white);border-color:var(--brand)}
.tab+.tab{border-left:none}
.field{height:20px;border:1px solid #888;display:flex;align-items:center;justify-content:space-between;padding:0 6px;font-size:8px;color:#333;background:var(--white)}
.field i{font-style:normal;font-size:6px}
.range-label{font-size:10.5px;color:#333}
.range{height:3px;background:#333}
.range .fill{position:absolute;left:0;top:0;height:3px;background:var(--accent)}
.range .knob{position:absolute;top:-2px;width:7px;height:7px;border-radius:50%;background:var(--accent)}

/* listing card */
.listing{left:100px;width:368px;height:140px;display:flex}
.listing .photo{width:199px;height:140px;position:relative;overflow:hidden;background:linear-gradient(180deg,#7fb2d8 0%,#c9b28a 42%,#d7c39b 55%,#4fb0c8 68%,#2e8cad 85%,#7a5a3c 100%)}
.badge-new{position:absolute;left:-22px;top:6px;width:80px;height:18px;background:var(--orange);transform:rotate(-45deg);color:var(--white);font-family:'Arvo',serif;font-size:9px;display:flex;align-items:center;justify-content:center}
.listing .info{width:169px;height:140px;background:var(--panel);position:relative}
.info .price{position:absolute;left:13px;top:7px;color:var(--accent-soft);font-size:16px;font-weight:400}
.info .title{position:absolute;left:13px;top:29px;color:var(--white);font-family:'Arvo',serif;font-size:11px}
.info .desc{position:absolute;left:13px;top:43px;width:150px;color:#e5e5e5;font-size:8px;line-height:10px}
.info .facts{position:absolute;left:13px;top:64px;display:flex;gap:10px;align-items:center;color:var(--accent-soft);font-size:11px}
.facts span{display:flex;align-items:center;gap:3px}
.info .rule{position:absolute;left:13px;right:12px;top:80px;height:1px;background:var(--panel-line)}
.info .actions{position:absolute;left:13px;top:86px;display:flex;gap:14px}
.agent{position:absolute;left:0;bottom:0;width:169px;height:36px;display:flex}
.agent .portrait{width:39px;height:36px;background:linear-gradient(180deg,#d9d9d9,#8c8c8c)}
.agent .who{flex:1;background:var(--accent);padding:2px 3px;color:var(--white)}
.who b{display:block;font-family:'Arvo',serif;font-weight:400;font-size:11px;line-height:12px}
.who small{display:block;font-size:7.5px;line-height:9px}
.agent .tools{width:22px;background:var(--accent);border-left:1px solid #5cc2f0;display:flex;flex-direction:column;align-items:center;justify-content:space-around}
.sep{left:100px;width:368px;height:1px;background:var(--line)}

/* pagination */
.pager{right:229px;top:985px;display:flex;gap:3px}
.pager a{height:12px;min-width:11px;padding:0 4px;background:var(--panel);color:var(--white);font-size:6.5px;display:flex;align-items:center;justify-content:center;text-decoration:none}
.pager a.on{background:var(--accent)}
.pager .gap{width:14px;border-bottom:1px dotted #999;height:10px}

/* sidebar */
.search{left:483px;top:95px;width:115px;height:163px;background:var(--brand)}
.search .stabs{display:flex;height:24px}
.stabs span{flex:1;display:flex;align-items:center;justify-content:center;text-align:center;color:var(--white);font-size:7px;line-height:8px;background:var(--brand-dark);border-left:1px solid #124d80}
.stabs span.on{background:var(--brand);border-left:none}
.search .sfield{position:absolute;left:8px;width:99px;height:17px;background:#eef1f4;font-size:6.5px;color:#555;padding:0 5px;display:flex;align-items:center;justify-content:space-between}
.search .cta{position:absolute;left:22px;top:130px;width:72px;height:19px;background:var(--white);color:var(--brand);font-size:8px;display:flex;align-items:center;justify-content:center}
.feat-head{left:483px;top:272px;font-family:'Arvo',serif;font-size:11px;font-weight:700;color:#222}
.feat{left:483px;width:115px;height:40px;display:flex;gap:6px;border-bottom:1px solid #e2e2e2}
.feat .thumb{width:30px;height:30px;background:linear-gradient(180deg,#6f86a0,#b79f7a 55%,#3c5f7d)}
.feat p{font-size:6.5px;line-height:7.5px;color:#444}
.feat b{display:block;font-family:'Arvo',serif;font-weight:400;font-size:8px;line-height:9px;color:#222}
.feat em{font-style:normal;color:var(--accent);font-size:7.5px}

/* footer */
.footer{left:0;top:1028px;width:698px;height:154px;background:var(--footer);color:#ddd}
.footer h4{position:absolute;top:19px;font-weight:400;font-size:8px;color:#aaa;text-transform:uppercase;letter-spacing:.3px}
.footer h4::after{content:"";position:absolute;left:0;top:14px;width:18px;height:1px;background:var(--accent)}
.find{position:absolute;left:101px;top:38px;width:112px;font-size:6.5px}
.find .lead{color:#8fd3f3;margin-bottom:8px}
.find li{list-style:none;display:flex;gap:7px;margin-bottom:8px;line-height:8px}
.flist{position:absolute;left:229px;top:38px;width:150px}
.flist .row{display:flex;gap:13px;height:33px;margin-bottom:3px}
.flist .ph{width:28px;height:28px;background:#4e4e50;display:flex;align-items:center;justify-content:center}
.flist p{font-size:6.5px;line-height:8px;color:#ddd;width:105px}
.flist em{font-style:normal;color:var(--accent)}
.cform .in{position:absolute;height:17px;background:#2f2f31;font-size:6.5px;color:#ddd;padding:4px 4px}
.cform .send{position:absolute;left:526px;top:118px;width:71px;height:20px;background:var(--accent);color:var(--white);font-size:8px;font-weight:600;display:flex;align-items:center;justify-content:center}
.legal{left:0;top:1182px;width:698px;height:18px;background:var(--footer-deep);color:#bbb;font-size:6px;display:flex;align-items:center;justify-content:center}
</style>
</head>
<body>

<header>
  <div class="abs topbar"></div>
  <div class="abs hero-band" role="img" aria-label="Soft coastal sky with a distant headland"><div class="ridge"></div></div>
  <div class="abs brand"><span>Marwick<br>on the Shore</span></div>
  <nav class="abs nav">
    <a href="#">Home</a>
    <a href="#" class="current">Properties <svg width="6" height="4" viewBox="0 0 6 4"><path d="M0 0l3 3 3-3" fill="none" stroke="currentColor"/></svg></a>
    <a href="#">Meet Our Team</a>
    <a href="#" style="margin-left:10px">Featured Listings <svg width="6" height="4" viewBox="0 0 6 4"><path d="M0 0l3 3 3-3" fill="none" stroke="currentColor"/></svg></a>
    <a href="#">Videos</a>
    <a href="#" style="margin-left:5px">Contact</a>
  </nav>
  <h1 class="abs page-title">Properties</h1>
</header>

<main>
  <div class="abs tabs">
    <div class="tab active">List with the Leader</div>
    <div class="tab">Previously Sold</div>
  </div>

  <div class="abs field" style="left:100px;top:129px;width:72px">Property ID</div>
  <div class="abs field" style="left:185px;top:129px;width:115px">Property Location <i>▼</i></div>
  <div class="abs field" style="left:312px;top:129px;width:86px">Property Type <i>▼</i></div>
  <div class="abs field" style="left:410px;top:129px;width:59px">Min Beds <i>▼</i></div>

  <div class="abs range-label" style="left:100px;top:157px">Price &nbsp;: &nbsp;$35,000,000</div>
  <div class="abs range" style="left:100px;top:177px;width:198px"><div class="fill" style="width:97px"></div><span class="knob" style="left:0"></span><span class="knob" style="left:94px"></span></div>
  <div class="abs range-label" style="left:312px;top:157px">Areas &nbsp;: &nbsp;100 ft2 - 200 ft2</div>
  <div class="abs range" style="left:312px;top:177px;width:156px"><div class="fill" style="width:70px"></div><span class="knob" style="left:0"></span><span class="knob" style="left:67px"></span></div>

  <!-- listings -->
  <article class="abs listing" style="top:193px">
    <div class="photo" role="img" aria-label="Mediterranean villa with infinity pool overlooking the ocean"><span class="badge-new">New</span></div>
    <div class="info">
      <div class="price">$35,000,000</div>
      <div class="title">Lorem Ipsum is simply</div>
      <div class="desc">dummy text of the printing and typeset-ting industry.</div>
      <div class="facts">
        <span><svg width="9" height="9" viewBox="0 0 9 9" fill="none" stroke="#17a3e6"><path d="M1 3V1h2M6 1h2v2M8 6v2H6M3 8H1V6"/></svg>5,825 ft2</span>
        <span><svg width="12" height="8" viewBox="0 0 12 8" fill="none" stroke="#999"><path d="M1 7V1M1 5h10v2M3 5V3h4v2"/></svg>4</span>
        <span><svg width="10" height="9" viewBox="0 0 10 9" fill="none" stroke="#999"><path d="M1 4h8v2a2 2 0 0 1-2 2H3a2 2 0 0 1-2-2zM2 4V1h2"/></svg>3</span>
      </div>
      <div class="rule"></div>
      <div class="actions">
        <svg width="11" height="10" viewBox="0 0 11 10" fill="none" stroke="#999"><path d="M5.5 9L1.5 5a2.2 2.2 0 0 1 4-3 2.2 2.2 0 0 1 4 3z"/></svg>
        <svg width="10" height="10" viewBox="0 0 10 10" fill="#999" stroke="#999"><circle cx="2" cy="5" r="1.4"/><circle cx="8" cy="2" r="1.4"/><circle cx="8" cy="8" r="1.4"/><path d="M2 5l6-3M2 5l6 3" fill="none"/></svg>
        <svg width="10" height="10" viewBox="0 0 10 10" stroke="#999"><path d="M5 0v10M0 5h10"/></svg>
      </div>
      <div class="agent">
        <div class="portrait" role="img" aria-label="Agent portrait"></div>
        <div class="who"><b>Dana Merritt</b><small>literature from 45 BC, making it over 2000 years</small></div>
        <div class="tools">
          <svg width="9" height="9" viewBox="0 0 9 9" fill="none" stroke="#fff"><path d="M4 1h4v7H4M1 4.5h5M4 3l2 1.5L4 6"/></svg>
          <svg width="7" height="9" viewBox="0 0 7 9" fill="none" stroke="#fff"><path d="M3.5 8.5S1 5.5 1 3.5a2.5 2.5 0 0 1 5 0c0 2-2.5 5-2.5 5z"/><circle cx="3.5" cy="3.5" r="1"/></svg>
        </div>
      </div>
    </div>
  </article>
  <div class="abs sep" style="top:342px"></div>

  <article class="abs listing" style="top:351px">
    <div class="photo" role="img" aria-label="Mediterranean villa with infinity pool overlooking the ocean"></div>
    <div class="info">
      <div class="price">$35,000,000</div>
      <div class="title">Lorem Ipsum is simply</div>
      <div class="desc">dummy text of the printing and typeset-ting industry.</div>
      <div class="facts">
        <span><svg width="9" height="9" viewBox="0 0 9 9" fill="none" stroke="#17a3e6"><path d="M1 3V1h2M6 1h2v2M8 6v2H6M3 8H1V6"/></svg>5,825 ft2</span>
        <span><svg width="12" height="8" viewBox="0 0 12 8" fill="none" stroke="#999"><path d="M1 7V1M1 5h10v2M3 5V3h4v2"/></svg>4</span>
        <span><svg width="10" height="9" viewBox="0 0 10 9" fill="none" stroke="#999"><path d="M1 4h8v2a2 2 0 0 1-2 2H3a2 2 0 0 1-2-2zM2 4V1h2"/></svg>3</span>
      </div>
      <div class="rule"></div>
      <div class="actions">
        <svg width="11" height="10" viewBox="0 0 11 10" fill="none" stroke="#999"><path d="M5.5 9L1.5 5a2.2 2.2 0 0 1 4-3 2.2 2.2 0 0 1 4 3z"/></svg>
        <svg width="10" height="10" viewBox="0 0 10 10" fill="#999" stroke="#999"><circle cx="2" cy="5" r="1.4"/><circle cx="8" cy="2" r="1.4"/><circle cx="8" cy="8" r="1.4"/><path d="M2 5l6-3M2 5l6 3" fill="none"/></svg>
        <svg width="10" height="10" viewBox="0 0 10 10" stroke="#999"><path d="M5 0v10M0 5h10"/></svg>
      </div>
      <div class="agent">
        <div class="portrait" role="img" aria-label="Agent portrait"></div>
        <div class="who"><b>Dana Merritt</b><small>literature from 45 BC, making it over 2000 years</small></div>
        <div class="tools">
          <svg width="9" height="9" viewBox="0 0 9 9" fill="none" stroke="#fff"><path d="M4 1h4v7H4M1 4.5h5M4 3l2 1.5L4 6"/></svg>
          <svg width="7" height="9" viewBox="0 0 7 9" fill="none" stroke="#fff"><path d="M3.5 8.5S1 5.5 1 3.5a2.5 2.5 0 0 1 5 0c0 2-2.5 5-2.5 5z"/><circle cx="3.5" cy="3.5" r="1"/></svg>
        </div>
      </div>
    </div>
  </article>
  <div class="abs sep" style="top:501px"></div>

  <article class="abs listing" style="top:510px">
    <div class="photo" role="img" aria-label="Mediterranean villa with infinity pool overlooking the ocean"><span class="badge-new">New</span></div>
    <div class="info">
      <div class="price">$35,000,000</div>
      <div class="title">Lorem Ipsum is simply</div>
      <div class="desc">dummy text of the printing and typeset-ting industry.</div>
      <div class="facts">
        <span><svg width="9" height="9" viewBox="0 0 9 9" fill="none" stroke="#17a3e6"><path d="M1 3V1h2M6 1h2v2M8 6v2H6M3 8H1V6"/></svg>5,825 ft2</span>
        <span><svg width="12" height="8" viewBox="0 0 12 8" fill="none" stroke="#999"><path d="M1 7V1M1 5h10v2M3 5V3h4v2"/></svg>4</span>
        <span><svg width="10" height="9" viewBox="0 0 10 9" fill="none" stroke="#999"><path d="M1 4h8v2a2 2 0 0 1-2 2H3a2 2 0 0 1-2-2zM2 4V1h2"/></svg>3</span>
      </div>
      <div class="rule"></div>
      <div class="actions">
        <svg width="11" height="10" viewBox="0 0 11 10" fill="none" stroke="#999"><path d="M5.5 9L1.5 5a2.2 2.2 0 0 1 4-3 2.2 2.2 0 0 1 4 3z"/></svg>
        <svg width="10" height="10" viewBox="0 0 10 10" fill="#999" stroke="#999"><circle cx="2" cy="5" r="1.4"/><circle cx="8" cy="2" r="1.4"/><circle cx="8" cy="8" r="1.4"/><path d="M2 5l6-3M2 5l6 3" fill="none"/></svg>
        <svg width="10" height="10" viewBox="0 0 10 10" stroke="#999"><path d="M5 0v10M0 5h10"/></svg>
      </div>
      <div class="agent">
        <div class="portrait" role="img" aria-label="Agent portrait"></div>
        <div class="who"><b>Dana Merritt</b><small>literature from 45 BC, making it over 2000 years</small></div>
        <div class="tools">
          <svg width="9" height="9" viewBox="0 0 9 9" fill="none" stroke="#fff"><path d="M4 1h4v7H4M1 4.5h5M4 3l2 1.5L4 6"/></svg>
          <svg width="7" height="9" viewBox="0 0 7 9" fill="none" stroke="#fff"><path d="M3.5 8.5S1 5.5 1 3.5a2.5 2.5 0 0 1 5 0c0 2-2.5 5-2.5 5z"/><circle cx="3.5" cy="3.5" r="1"/></svg>
        </div>
      </div>
    </div>
  </article>
  <div class="abs sep" style="top:660px"></div>

  <article class="abs listing" style="top:669px">
    <div class="photo" role="img" aria-label="Mediterranean villa with infinity pool overlooking the ocean"></div>
    <div class="info">
      <div class="price">$35,000,000</div>
      <div class="title">Lorem Ipsum is simply</div>
      <div class="desc">dummy text of the printing and typeset-ting industry.</div>
      <div class="facts">
        <span><svg width="9" height="9" viewBox="0 0 9 9" fill="none" stroke="#17a3e6"><path d="M1 3V1h2M6 1h2v2M8 6v2H6M3 8H1V6"/></svg>5,825 ft2</span>
        <span><svg width="12" height="8" viewBox="0 0 12 8" fill="none" stroke="#999"><path d="M1 7V1M1 5h10v2M3 5V3h4v2"/></svg>4</span>
        <span><svg width="10" height="9" viewBox="0 0 10 9" fill="none" stroke="#999"><path d="M1 4h8v2a2 2 0 0 1-2 2H3a2 2 0 0 1-2-2zM2 4V1h2"/></svg>3</span>
      </div>
      <div class="rule"></div>
      <div class="actions">
        <svg width="11" height="10" viewBox="0 0 11 10" fill="none" stroke="#999"><path d="M5.5 9L1.5 5a2.2 2.2 0 0 1 4-3 2.2 2.2 0 0 1 4 3z"/></svg>
        <svg width="10" height="10" viewBox="0 0 10 10" fill="#999" stroke="#999"><circle cx="2" cy="5" r="1.4"/><circle cx="8" cy="2" r="1.4"/><circle cx="8" cy="8" r="1.4"/><path d="M2 5l6-3M2 5l6 3" fill="none"/></svg>
        <svg width="10" height="10" viewBox="0 0 10 10" stroke="#999"><path d="M5 0v10M0 5h10"/></svg>
      </div>
      <div class="agent">
        <div class="portrait" role="img" aria-label="Agent portrait"></div>
        <div class="who"><b>Dana Merritt</b><small>literature from 45 BC, making it over 2000 years</small></div>
        <div class="tools">
          <svg width="9" height="9" viewBox="0 0 9 9" fill="none" stroke="#fff"><path d="M4 1h4v7H4M1 4.5h5M4 3l2 1.5L4 6"/></svg>
          <svg width="7" height="9" viewBox="0 0 7 9" fill="none" stroke="#fff"><path d="M3.5 8.5S1 5.5 1 3.5a2.5 2.5 0 0 1 5 0c0 2-2.5 5-2.5 5z"/><circle cx="3.5" cy="3.5" r="1"/></svg>
        </div>
      </div>
    </div>
  </article>
  <div class="abs sep" style="top:819px"></div>

  <article class="abs listing" style="top:828px">
    <div class="photo" role="img" aria-label="Mediterranean villa with infinity pool overlooking the ocean"><span class="badge-new">New</span></div>
    <div class="info">
      <div class="price">$35,000,000</div>
      <div class="title">Lorem Ipsum is simply</div>
      <div class="desc">dummy text of the printing and typeset-ting industry.</div>
      <div class="facts">
        <span><svg width="9" height="9" viewBox="0 0 9 9" fill="none" stroke="#17a3e6"><path d="M1 3V1h2M6 1h2v2M8 6v2H6M3 8H1V6"/></svg>5,825 ft2</span>
        <span><svg width="12" height="8" viewBox="0 0 12 8" fill="none" stroke="#999"><path d="M1 7V1M1 5h10v2M3 5V3h4v2"/></svg>4</span>
        <span><svg width="10" height="9" viewBox="0 0 10 9" fill="none" stroke="#999"><path d="M1 4h8v2a2 2 0 0 1-2 2H3a2 2 0 0 1-2-2zM2 4V1h2"/></svg>3</span>
      </div>
      <div class="rule"></div>
      <div class="actions">
        <svg width="11" height="10" viewBox="0 0 11 10" fill="none" stroke="#999"><path d="M5.5 9L1.5 5a2.2 2.2 0 0 1 4-3 2.2 2.2 0 0 1 4 3z"/></svg>
        <svg width="10" height="10" viewBox="0 0 10 10" fill="#999" stroke="#999"><circle cx="2" cy="5" r="1.4"/><circle cx="8" cy="2" r="1.4"/><circle cx="8" cy="8" r="1.4"/><path d="M2 5l6-3M2 5l6 3" fill="none"/></svg>
        <svg width="10" height="10" viewBox="0 0 10 10" stroke="#999"><path d="M5 0v10M0 5h10"/></svg>
      </div>
      <div class="agent">
        <div class="portrait" role="img" aria-label="Agent portrait"></div>
        <div class="who"><b>Dana Merritt</b><small>literature from 45 BC, making it over 2000 years</small></div>
        <div class="tools">
          <svg width="9" height="9" viewBox="0 0 9 9" fill="none" stroke="#fff"><path d="M4 1h4v7H4M1 4.5h5M4 3l2 1.5L4 6"/></svg>
          <svg width="7" height="9" viewBox="0 0 7 9" fill="none" stroke="#fff"><path d="M3.5 8.5S1 5.5 1 3.5a2.5 2.5 0 0 1 5 0c0 2-2.5 5-2.5 5z"/><circle cx="3.5" cy="3.5" r="1"/></svg>
        </div>
      </div>
    </div>
  </article>

  <nav class="abs pager">
    <a href="#" style="width:35px">Previous</a>
    <a href="#">1</a>
    <a href="#">2</a>
    <a href="#" class="on">3</a>
    <span class="gap"></span>
    <a href="#">8</a>
    <a href="#" style="width:29px">Next</a>
  </nav>
</main>

<aside>
  <div class="abs search">
    <div class="stabs"><span class="on">Selling</span><span>Buying</span><span>Previously<br>Sold</span></div>
    <div class="sfield" style="top:34px">Propertie Type</div>
    <div class="sfield" style="top:56px">Area</div>
    <div class="sfield" style="top:78px">Available From
      <svg width="8" height="7" viewBox="0 0 8 7" fill="none" stroke="#777"><rect x=".5" y="1" width="7" height="5.5"/><path d="M.5 3h7"/></svg></div>
    <div class="sfield" style="top:100px">Price</div>
    <div class="cta">Sell Your Home</div>
  </div>

  <h3 class="abs feat-head">Featured Properties</h3>
  <div class="abs feat" style="top:297px"><div class="thumb" role="img" aria-label="Waterfront home"></div><p><b>Lorem ipsum dolor</b>sit amet, consectetur adipiscing elit.<br><em>35,000,000</em></p></div>
  <div class="abs feat" style="top:342px"><div class="thumb" role="img" aria-label="Waterfront home"></div><p><b>Lorem ipsum dolor</b>sit amet, consectetur adipiscing elit.<br><em>35,000,000</em></p></div>
  <div class="abs feat" style="top:387px"><div class="thumb" role="img" aria-label="Waterfront home"></div><p><b>Lorem ipsum dolor</b>sit amet, consectetur adipiscing elit.<br><em>35,000,000</em></p></div>
  <div class="abs feat" style="top:431px"><div class="thumb" role="img" aria-label="Waterfront home"></div><p><b>Lorem ipsum dolor</b>sit amet, consectetur adipiscing elit.<br><em>35,000,000</em></p></div>
  <div class="abs feat" style="top:476px"><div class="thumb" role="img" aria-label="Waterfront home"></div><p><b>Lorem ipsum dolor</b>sit amet, consectetur adipiscing elit.<br><em>35,000,000</em></p></div>
  <div class="abs feat" style="top:520px;border-bottom:none"><div class="thumb" role="img" aria-label="Waterfront home"></div><p><b>Lorem ipsum dolor</b>sit amet, consectetur adipiscing elit.<br><em>35,000,000</em></p></div>
</aside>

<footer>
  <div class="abs footer">
    <h4 style="left:101px">Find Us</h4>
    <div class="find">
      <p class="lead">The standard Lorem Ipsum passage</p>
      <ul>
        <li><svg width="7" height="9" viewBox="0 0 7 9" fill="none" stroke="#ccc"><path d="M3.5 8.5S1 5.5 1 3.5a2.5 2.5 0 0 1 5 0c0 2-2.5 5-2.5 5z"/></svg>TLorem Ipsum is simply dummy text of the printing</li>
        <li><svg width="8" height="8" viewBox="0 0 8 8" fill="none" stroke="#ccc"><path d="M1.5 1h2l.5 2-1 .8a4 4 0 0 0 1.7 1.7l.8-1 2 .5v2A6 6 0 0 1 1.5 1z"/></svg>(00) 98-765-4321</li>
        <li><svg width="8" height="7" viewBox="0 0 8 7" fill="none" stroke="#ccc"><rect x=".5" y="1" width="7" height="5"/><path d="M.5 1l3.5 3 3.5-3"/></svg>info@marwickshore.example</li>
      </ul>
    </div>

    <h4 style="left:229px">Featured Listings</h4>
    <div class="flist">
      <div class="row"><div class="ph" role="img" aria-label="Listing photo"><svg width="12" height="10" viewBox="0 0 12 10" fill="#6b6b6d"><path d="M0 0h12v10H0z" fill="none" stroke="#6b6b6d"/><path d="M1 9l3.5-4 2.5 3 1.5-1.5L11 9z"/></svg></div><p>Lorem Ipsum is simply dummy text of the printing and typesetting<br><em>$35,000,000</em></p></div>
      <div class="row"><div class="ph" role="img" aria-label="Listing photo"><svg width="12" height="10" viewBox="0 0 12 10" fill="#6b6b6d"><path d="M0 0h12v10H0z" fill="none" stroke="#6b6b6d"/><path d="M1 9l3.5-4 2.5 3 1.5-1.5L11 9z"/></svg></div><p>Lorem Ipsum is simply dummy text of the printing and typesetting<br><em>$35,000,000</em></p></div>
      <div class="row"><div class="ph" role="img" aria-label="Listing photo"><svg width="12" height="10" viewBox="0 0 12 10" fill="#6b6b6d"><path d="M0 0h12v10H0z" fill="none" stroke="#6b6b6d"/><path d="M1 9l3.5-4 2.5 3 1.5-1.5L11 9z"/></svg></div><p>Lorem Ipsum is simply dummy text of the printing and typesetting<br><em>$35,000,000</em></p></div>
    </div>

    <h4 style="left:398px">Contact Us</h4>
    <div class="cform">
      <div class="in" style="left:398px;top:39px;width:199px">Name:</div>
      <div class="in" style="left:398px;top:59px;width:114px">Email:</div>
      <div class="in" style="left:519px;top:59px;width:78px">Phone:</div>
      <div class="in" style="left:398px;top:79px;width:199px;height:33px">Massage:</div>
      <div class="send">Submit</div>
    </div>
  </div>
  <div class="abs legal">Copyright © 2015. All Rights Reserved. Terms &amp; Conditions</div>
</footer>

</body>
</html>
```